Executive Business Card for Healthcare Company [Need Today]

I need a business card design for a healthcare company. The only branding the company has thus far is a logo. The cards will be utilized by company executives. The design I envision will be vibrant and appealing but with a corporate feel. They shouldn't be too casual or playful. I would like to complete this project TODAY if possible.

Target Market(s)

Healthcare vendors, other executives in healthcare and pharmaceuticals

Industry/Entity Type

Pharmaceutical

Contact Information for Business Card

See attachment

Font styles to use
Serif
Sans Serif

Colors

Designer to choose colors to be used in the design.

```html
<!DOCTYPE html>
<html lang="en">
<head>
<meta charset="utf-8">
<title>Corvane Therapeutics – Business Card</title>
<link rel="stylesheet" href="https://fonts.googleapis.com/css2?family=Roboto:wght@300;400;500&display=swap">
<style>
  :root {
    --backdrop: #3a3a3c;
    --card: #1f1f21;
    --emboss: #3b3b3e;
    --emboss-light: #6a6a6e;
    --teal: #1fb3c4;
    --green: #3dbf86;
    --muted-grey: #7c7c80;
    --text-light: #e6e6e6;
  }
  * { box-sizing: border-box; margin: 0; padding: 0; }
  html, body { width: 799px; height: 1200px; overflow: hidden; }
  body {
    background: var(--backdrop);
    font-family: "Roboto", sans-serif;
    position: relative;
  }
  .card {
    position: absolute;
    left: 80px;
    width: 640px;
    height: 366px;
    background: var(--card);
    border-radius: 4px;
    box-shadow: 0 14px 30px rgba(0,0,0,0.45);
    overflow: hidden;
  }
  .card--front { top: 120px; }
  .card--back { top: 700px; }

  .brand {
    position: absolute;
    display: flex;
    align-items: center;
    gap: 18px;
  }
  .brand__mark {
    width: 96px; height: 96px;
    border-radius: 50%;
    border: 3px solid currentColor;
  }
  .brand__divider {
    width: 1px; height: 70px;
    background: currentColor;
    opacity: 0.6;
  }
  .brand__name {
    font-weight: 300;
    line-height: 1;
  }
  .brand__name-main { display: block; font-size: 58px; letter-spacing: 1px; }
  .brand__name-sub { display: block; font-size: 28px; margin-top: 4px; letter-spacing: 1px; }

  .card--front .brand { left: 70px; top: 100px; color: var(--emboss-light); }
  .card--front .brand__mark { color: var(--emboss); }
  .website {
    position: absolute;
    left: 70px; bottom: 48px;
    color: var(--text-light);
    font-size: 18px;
    letter-spacing: 4px;
  }

  .card--back .brand { left: 34px; top: 34px; color: var(--teal); }
  .card--back .brand__mark { width: 84px; height: 84px; border-color: var(--green); }
  .card--back .brand__divider { background: var(--muted-grey); }
  .card--back .brand__name-main { font-size: 50px; }
  .card--back .brand__name-sub { font-size: 24px; color: var(--muted-grey); }

  .contact {
    position: absolute;
    right: 40px; top: 182px;
    width: 270px;
    color: var(--text-light);
  }
  .contact__name { color: var(--teal); font-size: 24px; font-weight: 500; }
  .contact__title { font-size: 12px; margin: 2px 0 10px; color: #cfcfcf; }
  .contact__line {
    display: flex; align-items: center; gap: 8px;
    font-size: 15px; line-height: 20px;
  }
  .contact__line svg { width: 13px; height: 13px; fill: #d8d8d8; flex: none; }
  .contact__address { font-size: 15px; line-height: 20px; margin-top: 2px; }

  .accent-band {
    position: absolute;
    left: 0; bottom: 0;
    width: 100%; height: 14px;
  }
</style>
</head>
<body>

<section class="card card--front">
  <div class="brand">
    <span class="brand__mark"></span>
    <span class="brand__divider"></span>
    <span class="brand__name">
      <span class="brand__name-main">corvane</span>
      <span class="brand__name-sub">therapeutics</span>
    </span>
  </div>
  <p class="website">www.corvanerx.com</p>
</section>

<section class="card card--back">
  <div class="brand">
    <span class="brand__mark"></span>
    <span class="brand__divider"></span>
    <span class="brand__name">
      <span class="brand__name-main">corvane</span>
      <span class="brand__name-sub">therapeutics</span>
    </span>
  </div>

  <div class="contact">
    <p class="contact__name">Daniel Mercer</p>
    <p class="contact__title">Senior Director of Marketing</p>
    <p class="contact__line">
      <svg viewBox="0 0 24 24"><path d="M6.6 10.8a15.1 15.1 0 0 0 6.6 6.6l2.2-2.2c.3-.3.7-.4 1-.2 1.1.4 2.3.6 3.6.6.6 0 1 .4 1 1V20c0 .6-.4 1-1 1A17 17 0 0 1 3 4c0-.6.4-1 1-1h3.5c.6 0 1 .4 1 1 0 1.2.2 2.4.6 3.6.1.3 0 .7-.2 1z"/></svg>
      555-210-4718
    </p>
    <p class="contact__line">
      <svg viewBox="0 0 24 24"><path d="M7 1h10a2 2 0 0 1 2 2v18a2 2 0 0 1-2 2H7a2 2 0 0 1-2-2V3a2 2 0 0 1 2-2zm0 3v14h10V4zm5 15.5a1 1 0 1 0 0 2 1 1 0 0 0 0-2z"/></svg>
      555-382-6054
    </p>
    <p class="contact__line">
      <svg viewBox="0 0 24 24"><path d="M12 2a10 10 0 1 0 0 20 10 10 0 0 0 0-20zm6.9 6h-3a15.7 15.7 0 0 0-1.3-3.6A8 8 0 0 1 18.9 8zM12 4c.8 1.2 1.5 2.5 1.9 4h-3.8c.4-1.5 1.1-2.8 1.9-4zM4.3 14a8 8 0 0 1 0-4h3.4a16 16 0 0 0 0 4zm.8 2h3a15.7 15.7 0 0 0 1.3 3.6A8 8 0 0 1 5.1 16zm3-8h-3a8 8 0 0 1 4.3-3.6C8.8 5.5 8.4 6.7 8.1 8zM12 20c-.8-1.2-1.5-2.5-1.9-4h3.8c-.4 1.5-1.1 2.8-1.9 4zm2.3-6H9.7a14 14 0 0 1 0-4h4.6a14 14 0 0 1 0 4zm.3 5.6c.6-1.1 1-2.3 1.3-3.6h3a8 8 0 0 1-4.3 3.6zm1.7-5.6a16 16 0 0 0 0-4h3.4a8 8 0 0 1 0 4z"/></svg>
      dmercer@corvanerx.com
    </p>
    <p class="contact__address">118 Linden Park Avenue<br>Brookfield, OH 44403</p>
  </div>

  <svg class="accent-band" viewBox="0 0 640 14" preserveAspectRatio="none" aria-hidden="true">
    <defs>
      <linearGradient id="band-gradient" x1="0" x2="1" y1="0" y2="0">
        <stop offset="0" stop-color="#1fb3c4"/>
        <stop offset="1" stop-color="#3dbf86"/>
      </linearGradient>
    </defs>
    <rect x="0" y="0" width="420" height="14" fill="url(#band-gradient)"/>
    <rect x="420" y="0" width="220" height="14" fill="#7c7c80"/>
  </svg>
</section>

</body>
</html>
```